Drifting Tide Chronicle - Book Cover Design

I need a cover (front, spine, back) designed for the second edition of the historical book - Drifting Tide Chronicle. This book was created to be a more engaging supplementary resource to the dry texts of most middle and high school social studies classrooms. Although comprehensive and exhaustively researched, the book at times uses humor and irony to engage the reader. The cover should reflect this tone.

Book Title: Drifting Tide Chronicle
Subtitle: The Tales, Traditions and Turning Points of World History and the Regional Challenges of Today
Author: Owen Halvorsen
Updates

Project Deadline Extended
Reason: As multiple designers are working on adjustments and I am looking for new, creative ideas, I am extending the deadline five days. Thank you.

Project Deadline Extended
Reason: Artists are still making alterations to suggestions made and I also want to give designers a chance to submit new ideas.

Target Market(s)

Middle School and High School Teachers

Font styles to use
Serif

Colors
ec1f27
ffffff
000000

Requirements
Must have
• 1) See attachment for text for front cover, spine, back cover
• 2) Central, engaging image
Nice to have
• A subtle hint of humor, light tone
• Potentially upside down globe spinning
• Prefer black, red, white color scheme
Should not have
• Cartoonish text, images

```html
<!DOCTYPE html>
<html lang="en">
<head>
<meta charset="utf-8">
<title>Drifting Tide Chronicle — Front Cover</title>
<link href="https://fonts.googleapis.com/css2?family=Cinzel:wght@400;500&family=Amatic+SC:wght@700&display=swap" rel="stylesheet">
<style>
  :root {
    --red: #ec1f27;
    --white: #ffffff;
    --black: #000000;
    --backdrop: #f1f1f1;
    --globe-light: #cfcac0;
    --globe-mid: #8d887d;
    --brass: #8a7646;
  }
  html, body {
    margin: 0;
    padding: 0;
    width: 1200px;
    height: 1200px;
    overflow: hidden;
    background: var(--backdrop);
  }
  .cover {
    position: absolute;
    left: 250px;
    top: 50px;
    width: 700px;
    height: 1100px;
    background: var(--black);
    text-align: center;
    color: var(--white);
    overflow: hidden;
  }
  .title {
    position: absolute;
    top: 40px;
    left: 0;
    right: 0;
    margin: 0;
    font-family: "Cinzel", "Trajan Pro", serif;
    font-weight: 400;
    font-size: 98px;
    line-height: 148px;
    color: var(--red);
    letter-spacing: 1px;
  }
  .title-line {
    display: block;
    text-shadow: -14px -10px 10px rgba(236, 31, 39, 0.45), -28px -20px 16px rgba(236, 31, 39, 0.25);
  }
  .title-light {
    color: var(--white);
    text-shadow: -14px -10px 10px rgba(255, 255, 255, 0.3), -28px -20px 16px rgba(255, 255, 255, 0.15);
  }
  .subtitle {
    position: absolute;
    top: 522px;
    left: 40px;
    right: 40px;
    margin: 0;
    font-family: "Amatic SC", "Arial Narrow", sans-serif;
    font-weight: 700;
    font-size: 27px;
    line-height: 36px;
    letter-spacing: 1.5px;
    text-transform: uppercase;
    color: var(--white);
  }
  .globe-art {
    position: absolute;
    left: 225px;
    top: 615px;
    width: 250px;
    height: 370px;
  }
  .author {
    position: absolute;
    bottom: 30px;
    left: 0;
    right: 0;
    margin: 0;
    font-family: "Cinzel", "Trajan Pro", serif;
    font-weight: 400;
    font-size: 60px;
    line-height: 80px;
    color: var(--red);
    text-shadow: -10px -8px 9px rgba(236, 31, 39, 0.4);
  }
</style>
</head>
<body>
  <main class="cover">
    <h1 class="title">
      <span class="title-line"><span class="title-light">DRIFT</span>ING</span>
      <span class="title-line">TIDE</span>
      <span class="title-line">CHRONICLE</span>
    </h1>
    <p class="subtitle">The Tales, Traditions and Turning Points of World History<br>and the Regional Challenges of Today</p>
    <svg class="globe-art" viewBox="0 0 250 370" role="img" aria-label="Photograph of an antique desk globe on a brass stand, spinning with motion blur">
      <defs>
        <radialGradient id="globe-tone" cx="0.5" cy="0.4" r="0.6">
          <stop offset="0" stop-color="var(--globe-light)"/>
          <stop offset="0.45" stop-color="var(--globe-mid)"/>
          <stop offset="0.8" stop-color="var(--brass)" stop-opacity="0.5"/>
          <stop offset="1" stop-color="var(--black)" stop-opacity="0"/>
        </radialGradient>
      </defs>
      <rect x="0" y="0" width="250" height="370" fill="url(#globe-tone)"/>
    </svg>
    <p class="author">OWEN HALVORSEN</p>
  </main>
</body>
</html>
```